Flask Mint Studio needs wedding label designs!

Flask Mint Studio is looking for new wedding designs! Please look at http://www.flaskmintstudio.com/water-bottle-labels and http://www.flaskmintstudio.com/custom-water to get an idea of what we currently offer.

These new designs will be saved onto Flask Mint Studio so that customers can come and customize the text and/or add pictures on them for purchase as water bottle labels or custom label bottled water.

Designs must appeal to a broad audience so any and all styles will be considered. Some other sites to draw inspiration from are plumcards.com, velvora.com, altarinkqueens.com and fernly.com.

Questions? Ask away!

Target Market(s)

Target market is brides, mothers of brides and wedding planners.

Industry/Entity Type

Wedding

Requirements
Must have
• Designs must be at 300 dpi in CMYK. Width is 8.133" Height is 2.377" with a .125" bleed around all sides.

```html
<!DOCTYPE html>
<html lang="en">
<head>
<meta charset="utf-8">
<title>Wedding Water Bottle Labels</title>
<link rel="stylesheet" href="https://fonts.googleapis.com/css2?family=Roboto+Condensed&family=PT+Sans:ital,wght@1,700&family=Kaushan+Script&display=swap">
<style>
  :root {
    --board-light: #ffffff;
    --board-dark: #c9c9c9;
    --caption: #7a7a7a;
    --cream: #f6f0e3;
    --floral-tan: #ddd4b7;
    --olive: #a09561;
    --olive-text: #9a8d5d;
    --slate-blue: #4f7483;
    --ornament-tint: #dfe4de;
    --coral: #f47f57;
    --swirl-red: #d6523b;
    --crimson: #c0282d;
    --white: #ffffff;
  }
  html, body {
    margin: 0;
    width: 1200px;
    height: 900px;
    overflow: hidden;
  }
  body {
    position: relative;
    background: radial-gradient(ellipse at 50% 45%, var(--board-light) 45%, var(--board-dark) 100%);
    font-family: "PT Sans", sans-serif;
  }
  .design-code {
    position: absolute;
    left: 131px;
    margin: 0;
    font-family: "Roboto Condensed", sans-serif;
    font-size: 20px;
    font-weight: 400;
    color: var(--caption);
    letter-spacing: 0.3px;
  }
  .design-code--garden { top: 84px; }
  .design-code--coral { top: 455px; }

  .label {
    position: absolute;
    left: 131px;
    width: 938px;
    height: 274px;
    overflow: hidden;
    box-shadow: 3px 4px 6px rgba(0, 0, 0, 0.28);
  }
  .label--garden { top: 120px; }
  .label--coral { top: 491px; }

  .pattern {
    position: absolute;
    inset: 0;
  }
  .label--garden .pattern {
    background: linear-gradient(90deg, var(--floral-tan), var(--cream) 30%, var(--floral-tan) 55%, var(--cream) 80%, var(--floral-tan));
  }
  .label--coral .pattern {
    background: linear-gradient(90deg, var(--swirl-red), var(--coral) 25%, var(--coral) 75%, var(--swirl-red));
  }

  .band-set {
    position: absolute;
    left: 0;
    top: 67px;
    width: 100%;
    height: 139px;
  }
  .band {
    position: absolute;
    left: 0;
    width: 100%;
  }
  .band--olive-top { top: 0; height: 16px; background: var(--olive); }
  .band--blue-top { top: 16px; height: 8px; background: var(--slate-blue); }
  .band--cream { top: 24px; height: 92px; background: var(--cream); }
  .band--blue-bottom { top: 116px; height: 8px; background: var(--slate-blue); }
  .band--olive-bottom { top: 124px; height: 15px; background: var(--olive); }

  .ornament {
    position: absolute;
    top: 100px;
    width: 82px;
    height: 84px;
    border-radius: 40% 40% 30% 30%;
    background: var(--ornament-tint);
  }
  .ornament--left { left: 219px; }
  .ornament--right { left: 637px; }

  .couple-block {
    position: absolute;
    left: 0;
    width: 100%;
    text-align: center;
  }
  .label--garden .couple-block { top: 102px; color: var(--olive-text); }
  .label--garden .couple-names {
    margin: 0;
    font-size: 39px;
    font-weight: 700;
    font-style: italic;
    line-height: 46px;
    letter-spacing: -0.3px;
  }
  .label--garden .wedding-date {
    margin: 0;
    font-size: 22px;
    font-weight: 700;
    font-style: italic;
    line-height: 26px;
  }

  .medallion {
    position: absolute;
    left: 290px;
    top: 34px;
    width: 356px;
    height: 206px;
  }
  .label--coral .couple-block {
    top: 100px;
    color: var(--crimson);
    font-family: "Kaushan Script", cursive;
  }
  .label--coral .couple-names {
    margin: 0;
    font-size: 39px;
    font-weight: 400;
    line-height: 50px;
  }
  .label--coral .wedding-date {
    margin: 0;
    font-size: 22px;
    font-weight: 400;
    line-height: 30px;
    letter-spacing: 1.5px;
  }
</style>
</head>
<body>
  <p class="design-code design-code--garden">WBL03</p>
  <section class="label label--garden">
    <div class="pattern" role="img" aria-label="Faint tan botanical pattern of leaves and flowers on cream"></div>
    <div class="band-set">
      <div class="band band--olive-top"></div>
      <div class="band band--blue-top"></div>
      <div class="band band--cream"></div>
      <div class="band band--blue-bottom"></div>
      <div class="band band--olive-bottom"></div>
    </div>
    <div class="ornament ornament--left" role="img" aria-label="Slate blue line-drawn clover ornament"></div>
    <div class="ornament ornament--right" role="img" aria-label="Slate blue line-drawn clover ornament"></div>
    <div class="couple-block">
      <p class="couple-names">Helen &amp; Richard</p>
      <p class="wedding-date">May 21, 2011</p>
    </div>
  </section>

  <p class="design-code design-code--coral">WBL04</p>
  <section class="label label--coral">
    <div class="pattern" role="img" aria-label="Red flourish swirl pattern on coral"></div>
    <svg class="medallion" viewBox="0 0 356 206" aria-hidden="true">
      <ellipse cx="178" cy="103" rx="178" ry="103" fill="var(--crimson)"/>
      <ellipse cx="178" cy="103" rx="165" ry="90" fill="var(--white)"/>
    </svg>
    <div class="couple-block">
      <p class="couple-names">Helen &amp; Richard</p>
      <p class="wedding-date">May 21, 2011</p>
    </div>
  </section>
</body>
</html>
```